jQuery Mobile CSS for web app

Task Outline:
Create jQuery Mobile themeroller compliant CSS and icons for a mobile web app.
Task Description:
Brindle Solutions are in the process of implementing a new, web based version of their Tessel operations platform.
The web based version of Tessel is built on top of the jQuery Mobile platform and we are looking for a designer to create a jQuery Mobile themeroller compliant CSS theme pack that we can plug into our application. The aim is to remove the standard jQuery Mobile look and feel and to introduce the Brindle branding throughout the new web app.
A number of screenshots are shown in the attached design spec (brindle_solutions.pdf) that show what the current (Windows Mobile 6.5) application looks like, alongside the development version of our new web app.
Deliverables:
• jQuery Mobile (v 1.4.2) themeroller compliant CSS which provides theming for all jQuery Mobile UI components.
• Example html showing how to use the CSS theme (especially where additional html/css classes are required).
• New set of status icons (as listed in attachment)
Inspiration:
See our website for current branding: www.brindle-solutions-demo.net

```html
<!DOCTYPE html>
<html lang="en">
<head>
<meta charset="utf-8">
<title>Brindle – Labor</title>
<link rel="stylesheet" href="https://fonts.googleapis.com/css2?family=Open+Sans:wght@400;600&display=swap">
<style>
  :root {
    --bar-top: #2b2b2b;
    --bar-bottom: #1f1f1f;
    --page-bg: #1b1b1b;
    --row-bg: #1c1c1c;
    --row-line: #2b2b2b;
    --divider: #3a3a3a;
    --text-muted: #9b9b9b;
    --text-light: #ffffff;
    --nav-active: #c9c9c9;
    --nav-icon: #9a9a9a;
    --nav-icon-dark: #111111;
  }
  * { box-sizing: border-box; margin: 0; padding: 0; }
  html, body {
    width: 830px; height: 1200px; overflow: hidden;
    background: var(--page-bg);
    font-family: "Open Sans", Arial, sans-serif;
  }
  .app { position: relative; width: 830px; height: 1200px; background: var(--page-bg); }

  .app-header {
    position: absolute; top: 0; left: 0; width: 830px; height: 120px;
    background: linear-gradient(var(--bar-top), var(--bar-bottom));
    border-bottom: 2px solid #141414;
  }
  .brand {
    position: absolute; left: 38px; top: 22px;
    font-size: 48px; font-weight: 400; color: var(--text-light);
    letter-spacing: 0.5px; line-height: 1;
  }
  .header-divider {
    position: absolute; top: 24px; width: 1px; height: 70px; background: var(--divider);
  }
  .header-divider.left { left: 277px; }
  .header-divider.right { left: 729px; }
  .page-title {
    position: absolute; left: 315px; top: 48px;
    font-size: 19px; color: var(--text-light); line-height: 1;
  }
  .menu-button { position: absolute; left: 762px; top: 40px; }

  .labor-list { position: absolute; top: 122px; left: 0; width: 830px; list-style: none; }
  .labor-item {
    height: 124px; display: flex; align-items: center;
    padding-left: 50px; background: var(--row-bg);
    border-bottom: 3px solid var(--row-line);
    font-size: 25px; color: var(--text-muted);
  }

  .app-footer {
    position: absolute; left: 0; bottom: 0; width: 830px; height: 117px;
    display: flex; background: linear-gradient(var(--bar-top), var(--bar-bottom));
  }
  .nav-button {
    position: relative; flex: 1; display: flex; align-items: center; justify-content: center;
    border-left: 2px solid #141414;
  }
  .nav-button:first-child { border-left: none; }
  .nav-button.active { background: var(--nav-active); }
  .device-code {
    position: absolute; right: 28px; top: 50px;
    font-size: 17px; color: var(--text-light);
  }
</style>
</head>
<body>
<div class="app">
  <header class="app-header">
    <div class="brand">Brindle</div>
    <span class="header-divider left"></span>
    <h1 class="page-title">LABOR</h1>
    <span class="header-divider right"></span>
    <svg class="menu-button" width="36" height="34" viewBox="0 0 36 34" aria-label="Menu">
      <rect x="0" y="0" width="36" height="4" fill="#fff"/>
      <rect x="0" y="15" width="36" height="4" fill="#fff"/>
      <rect x="0" y="30" width="36" height="4" fill="#fff"/>
    </svg>
  </header>

  <ul class="labor-list">
    <li class="labor-item">2x Field Foreman</li>
    <li class="labor-item">1x Master Electrician</li>
    <li class="labor-item">2x Field Supervisor</li>
    <li class="labor-item">10x Pusher</li>
  </ul>

  <nav class="app-footer">
    <div class="nav-button active">
      <svg width="72" height="48" viewBox="0 0 72 48" aria-label="Back">
        <path d="M14 10 H52 A16 16 0 0 1 52 42 H22" fill="none" stroke="var(--nav-icon-dark)" stroke-width="5"/>
        <path d="M2 10 L18 0 V20 Z" fill="var(--nav-icon-dark)"/>
      </svg>
    </div>
    <div class="nav-button">
      <svg width="80" height="40" viewBox="0 0 80 40" aria-label="Home">
        <path d="M3 37 V16 L40 3 L77 16 V37 Z" fill="none" stroke="var(--nav-icon)" stroke-width="4"/>
      </svg>
    </div>
    <div class="nav-button">
      <svg width="72" height="48" viewBox="0 0 72 48" aria-label="Forward">
        <path d="M58 10 H20 A16 16 0 0 0 20 42 H50" fill="none" stroke="var(--nav-icon)" stroke-width="6"/>
        <path d="M70 10 L52 -1 V21 Z" fill="var(--nav-icon)"/>
      </svg>
      <span class="device-code">C8</span>
    </div>
  </nav>
</div>
</body>
</html>
```